sydney wedding photography business needs a business card design

we need a business card design for a sydney based wedding photography and videography business. our business name is :golden hour studio and film. our target clients are 24-35 yrs female. our style is candid, organic, natural, dynamic. we are a team of young photographers and videographers, and help brides to create memories that they will cherish for the rest of their lives. the logo will be provided. we want an elegant design that reflects our style, and also want to give a great impression to our clients that we are one of the best studios in sydney and our brand means quality and premium service.

Target Market(s)

bride to be, 24-35 years old, living in sydney and surrunding areas

Industry/Entity Type

Wedding Photography

Contact Information for Business Card

address: 57 tarrant street, glenmore nsw 2047
mobile: 0431872259
phone: (02) 9163 2408
info@tidewillowstudio.net.au
www.tidewillowstudio.net.au
facebook:tidewillowweddings
instagram:tidewillowweddings

Font styles to use
Serif
Sans Serif

Requirements
Nice to have
• maybe add my slogan"memories beyond eternity" if the layout looks good
Should not have
• no black color, not good idea for wedding biz card

```html
<!DOCTYPE html>
<html lang="en">
<head>
<meta charset="utf-8">
<title>Golden Hour Studio and Film — Business Card</title>
<link href="https://fonts.googleapis.com/css2?family=Montserrat:wght@400;500;600&display=swap" rel="stylesheet">
<style>
  :root {
    --stage: #e4ddd2;
    --card-light: #fbf6ec;
    --card-warm: #f1e6d2;
    --gold: #a97b22;
    --gold-deep: #8d6518;
    --text-body: #4e4338;
  }
  * { box-sizing: border-box; margin: 0; padding: 0; }
  html, body {
    width: 1200px; height: 843px; overflow: hidden;
    background: var(--stage);
    font-family: "Montserrat", Arial, sans-serif;
  }
  .stage {
    width: 1200px; height: 843px;
    display: flex; align-items: center; justify-content: center; gap: 60px;
  }
  .card {
    position: relative;
    width: 530px; height: 303px;
    background: linear-gradient(160deg, var(--card-light) 0%, var(--card-warm) 100%);
    border-radius: 3px;
    box-shadow: 0 10px 28px rgba(60,40,20,.22);
    overflow: hidden;
  }
  .brand {
    color: var(--gold);
    font-weight: 600;
    text-align: center;
    line-height: 1.05;
  }
  .brand-name { display: block; font-size: 32px; letter-spacing: .5px; }
  .brand-sub { display: block; font-size: 13px; letter-spacing: 6px; margin-top: 6px; }

  .card-front .brand {
    position: absolute; left: 0; right: 0; top: 50%;
    transform: translateY(-50%);
  }

  .card-back .brand {
    position: absolute; left: 120px; right: 40px; top: 40px;
  }

  .rule { position: absolute; height: 1.5px; background: var(--gold); }
  .rule-left { left: 26px; top: 131px; width: 156px; }
  .rule-right { left: 330px; right: 30px; top: 172px; }

  .holder {
    position: absolute; left: 192px; top: 120px;
    color: var(--gold-deep); font-size: 16px; font-weight: 500; white-space: nowrap;
    line-height: 22px;
  }
  .holder .role { color: var(--text-body); font-weight: 400; font-size: 14px; }

  .contacts {
    position: absolute; left: 26px; top: 142px;
    list-style: none; color: var(--text-body); font-size: 13px;
  }
  .contacts li { display: flex; align-items: center; gap: 9px; height: 20px; }
  .contacts svg { width: 13px; height: 13px; fill: var(--gold); flex: none; }

  .location {
    position: absolute; right: 30px; bottom: 30px;
    color: var(--text-body); font-size: 13px; text-align: right; line-height: 1.5;
    font-style: normal;
  }
</style>
</head>
<body>
<main class="stage">
  <section class="card card-front" aria-label="Business card front">
    <h1 class="brand">
      <span class="brand-name">Golden Hour</span>
      <span class="brand-sub">STUDIO AND FILM</span>
    </h1>
  </section>

  <section class="card card-back" aria-label="Business card back">
    <h2 class="brand">
      <span class="brand-name">Golden Hour</span>
      <span class="brand-sub">STUDIO AND FILM</span>
    </h2>

    <div class="rule rule-left"></div>
    <p class="holder">Liam Carter <span class="role">- President</span></p>
    <div class="rule rule-right"></div>

    <ul class="contacts">
      <li>
        <svg viewBox="0 0 16 16" aria-hidden="true"><path d="M3 1h3l1.5 4-2 1.3a9 9 0 0 0 4.2 4.2L11 8.5l4 1.5v3a2 2 0 0 1-2 2A13 13 0 0 1 1 3a2 2 0 0 1 2-2z"/></svg>
        (02) 9163 2408
      </li>
      <li>
        <svg viewBox="0 0 16 16" aria-hidden="true"><path d="M4.5 0h7A1.5 1.5 0 0 1 13 1.5v13a1.5 1.5 0 0 1-1.5 1.5h-7A1.5 1.5 0 0 1 3 14.5v-13A1.5 1.5 0 0 1 4.5 0zM5 2v10h6V2zm3 11a1 1 0 1 0 0 2 1 1 0 0 0 0-2z"/></svg>
        (04) 3187 2259
      </li>
      <li>
        <svg viewBox="0 0 16 16" aria-hidden="true"><path d="M0 3h16v1.2L8 9 0 4.2zM0 5.8l8 4.8 8-4.8V13H0z"/></svg>
        info@tidewillowstudio.net.au
      </li>
    </ul>

    <address class="location">
      57 tarrant street<br>
      glenmore nsw 2047<br>
      www.tidewillowstudio.net.au
    </address>
  </section>
</main>
</body>
</html>
```